Breakfast Cafe - The Sunny Nook

It is for my breakfast and lunch cafe with a hawaiian / beach theme. I am open 7 days a week from 7am to 2pm. We serve traditional American food such as omelettes, pancakes, burgers and sandwiches. I'll upload my old card and my new logo to be used. We have a lot of day to day regulars who eat there during the week, our t-shirts actually say 'Locals Only' on them. Hope this helps. Thanks.

Target Market(s)

anyone who has an appetite!

Industry/Entity Type

American Restaurant

Contact Information for Business Card

4815C Marlow Grove Avenue
Long Beach, California
(555) 731-2294

Requirements
Must have
• Address and phone number easily readable.
Nice to have
• beach or tropical theme

```html
<!DOCTYPE html>
<html lang="en">
<head>
<meta charset="utf-8">
<title>The Sunny Nook – Business Card</title>
<link rel="stylesheet" href="https://fonts.googleapis.com/css2?family=Roboto:ital,wght@0,400;0,500;0,700;1,400&display=swap">
<style>
  :root {
    --page-bg: #8a8a8a;
    --card-orange: #b8691d;
    --card-orange-dark: #a45a15;
    --band-blue: #5bbfd4;
    --name-blue: #47b3cc;
    --cream: #fdf5e8;
    --cream-arc: #ffffff;
    --brown: #9c5418;
    --white: #ffffff;
  }
  * { margin: 0; padding: 0; box-sizing: border-box; }
  html, body { width: 1000px; height: 1200px; overflow: hidden; }
  body {
    background: var(--page-bg);
    font-family: "Roboto", Arial, sans-serif;
    position: relative;
  }
  .card {
    position: absolute;
    width: 578px;
    height: 355px;
    overflow: hidden;
    box-shadow: 3px 4px 6px rgba(0,0,0,0.45);
  }
  /* Front */
  .card-front {
    left: 215px; top: 220px;
    background: var(--card-orange);
    border-radius: 0 42px 0 42px;
  }
  .front-art {
    position: absolute; inset: 0;
    background: radial-gradient(ellipse at 50% 85%, var(--card-orange-dark) 0%, var(--card-orange) 55%);
  }
  .front-phone {
    position: absolute; top: 46px; left: 0; right: 0;
    text-align: center; color: var(--white);
    font-size: 21px; font-weight: 500;
  }
  .front-band {
    position: absolute; top: 100px; left: 0; right: 0; height: 153px;
    background: var(--band-blue);
    text-align: center; color: var(--white);
  }
  .front-band .business-name {
    margin-top: 22px;
    font-size: 44px; font-weight: 700; letter-spacing: 1px;
    line-height: 1.1;
  }
  .front-band .city {
    margin-top: 6px;
    font-size: 14px; font-weight: 700; letter-spacing: 5px;
  }
  .front-band .tagline {
    margin-top: 10px;
    font-size: 18px; font-style: italic;
  }
  .front-hours {
    position: absolute; top: 286px; left: 0; right: 0;
    text-align: center; color: var(--white);
    font-size: 19px; font-weight: 500;
  }
  /* Back */
  .card-back {
    left: 213px; top: 607px;
    width: 580px;
    background: var(--cream);
    border-radius: 42px 0 42px 0;
  }
  .back-art {
    position: absolute; inset: 0;
    background: linear-gradient(100deg, #e6f1ee 0%, var(--cream) 35%, var(--cream) 70%, #f6ead6 100%);
  }
  .back-arc { position: absolute; inset: 0; }
  .back-content {
    position: absolute; top: 50px; left: 0; right: 0;
    text-align: center;
  }
  .brand-dot {
    width: 170px; height: 170px; margin: 0 auto;
    border-radius: 50%;
    background: radial-gradient(circle at 50% 40%, #f4b04a 0%, #e58f2c 55%, #8a5426 100%);
  }
  .back-content .business-name {
    margin-top: 14px;
    font-size: 32px; font-weight: 700; color: var(--name-blue);
  }
  .back-content .city {
    margin-top: 4px;
    font-size: 10px; font-weight: 700; letter-spacing: 3px; color: var(--brown);
  }
  .address {
    margin-top: 22px;
    font-size: 16px; line-height: 21px; color: var(--brown);
  }
</style>
</head>
<body>
  <section class="card card-front">
    <div class="front-art" role="img" aria-label="Faint tropical illustration of palm leaves, tiki carving and seagulls"></div>
    <p class="front-phone">Phone : (555) 731-2294</p>
    <div class="front-band">
      <p class="business-name">The Sunny Nook</p>
      <p class="city">LONG BEACH, CA</p>
      <p class="tagline">Family owned and operated!</p>
    </div>
    <p class="front-hours">Breakfast &amp; Lunch 7am - 2pm Daily</p>
  </section>

  <section class="card card-back">
    <div class="back-art" role="img" aria-label="Faint beach illustration with palm tree, sun rays, seagulls and a ship"></div>
    <svg class="back-arc" width="580" height="355" viewBox="0 0 580 355" aria-hidden="true">
      <path d="M-20 150 Q290 -60 600 150" fill="none" stroke="var(--cream-arc)" stroke-width="12"/>
    </svg>
    <div class="back-content">
      <div class="brand-dot"></div>
      <p class="business-name">The Sunny Nook</p>
      <p class="city">LONG BEACH, CA</p>
      <p class="address">4815C Marlow Grove Avenue<br>Long Beach, California</p>
    </div>
  </section>
</body>
</html>
```